Brellwick Partners, LLC Stationary

Brellwick Partners, LLC is a new financial planning and consulting company. We are looking for designs on business cards, letterhead, envelopes, and anything else that would be useful. Our preference for business card design is two sided. We are looking for a professional and clean look with incorporating the logo and patriotic feel. Thank you to all who participate and good luck!

```html
<!DOCTYPE html>
<html lang="en">
<head>
<meta charset="utf-8">
<title>Brellwick Partners, LLC – Business Card</title>
<link rel="stylesheet" href="https://fonts.googleapis.com/css2?family=Open+Sans:wght@400;600&display=swap">
<style>
  :root {
    --page: #e8e5e1;
    --navy-deep: #14223f;
    --navy: #243a63;
    --navy-soft: #34507f;
    --frost: #dcdbd8;
    --frost-light: #eeedea;
    --brand-navy: #1d2c55;
    --brand-red: #9c1c22;
    --ink-light: #f4f6fa;
    --ink-muted: #c9d2e2;
  }
  html, body {
    margin: 0;
    width: 1200px;
    height: 969px;
    overflow: hidden;
    background: var(--page);
    font-family: "Open Sans", Arial, sans-serif;
  }
  .business-card {
    position: absolute;
    left: 100px;
    top: 200px;
    width: 1000px;
    height: 568px;
    border-radius: 4px;
    overflow: hidden;
    background: linear-gradient(135deg, var(--frost-light), var(--frost));
    box-shadow: 0 10px 30px rgba(20, 34, 63, 0.18);
  }
  .card-field {
    position: absolute;
    inset: 0;
    width: 100%;
    height: 100%;
  }
  .holder {
    position: absolute;
    left: 60px;
    top: 58px;
    color: var(--ink-light);
  }
  .holder-name {
    margin: 0;
    font-size: 33px;
    font-weight: 600;
    letter-spacing: 1px;
  }
  .holder-title {
    margin: 4px 0 0;
    font-size: 24px;
    font-weight: 400;
    letter-spacing: 1px;
    color: var(--ink-muted);
  }
  .address {
    position: absolute;
    left: 60px;
    top: 272px;
    margin: 0;
    font-style: normal;
    font-size: 26px;
    line-height: 38px;
    color: var(--ink-light);
  }
  .contact-list {
    position: absolute;
    left: 60px;
    top: 362px;
    margin: 0;
    padding: 0;
    list-style: none;
    font-size: 25px;
    line-height: 39px;
    color: var(--ink-light);
  }
  .contact-list li {
    display: flex;
    align-items: center;
    gap: 12px;
  }
  .contact-list .web { color: var(--ink-muted); }
  .contact-icon {
    width: 22px;
    height: 22px;
    fill: var(--ink-muted);
    flex: none;
  }
  .brand {
    position: absolute;
    left: 520px;
    top: 238px;
    width: 430px;
    display: flex;
    align-items: flex-start;
    gap: 14px;
  }
  .brand-mark {
    width: 30px;
    height: 30px;
    margin-top: 18px;
    background: var(--brand-navy);
    flex: none;
  }
  .brand-text {
    display: flex;
    flex-direction: column;
    align-items: center;
  }
  .brand-name {
    margin: 0;
    font-size: 50px;
    line-height: 62px;
    font-weight: 600;
    color: var(--brand-navy);
    letter-spacing: 1px;
    white-space: nowrap;
  }
  .brand-suffix {
    margin: 0;
    font-size: 20px;
    line-height: 26px;
    font-weight: 600;
    letter-spacing: 4px;
    color: var(--brand-navy);
    white-space: nowrap;
  }
  .brand-tagline {
    margin: 4px 0 0;
    font-size: 11px;
    letter-spacing: 1.5px;
    text-transform: uppercase;
    color: var(--brand-navy);
    white-space: nowrap;
  }
</style>
</head>
<body>
  <section class="business-card" aria-label="Brellwick Partners business card">
    <svg class="card-field" viewBox="0 0 1000 568" aria-hidden="true">
      <defs>
        <linearGradient id="navyPanel" x1="0" y1="0" x2="1" y2="1">
          <stop offset="0" stop-color="var(--navy-deep)"/>
          <stop offset="0.45" stop-color="var(--navy-soft)"/>
          <stop offset="1" stop-color="var(--navy)"/>
        </linearGradient>
      </defs>
      <polygon points="0,0 620,0 470,210 760,568 0,568" fill="url(#navyPanel)"/>
      <line x1="620" y1="0" x2="470" y2="210" stroke="#ffffff" stroke-opacity="0.25" stroke-width="2"/>
      <line x1="470" y1="210" x2="760" y2="568" stroke="#ffffff" stroke-opacity="0.25" stroke-width="2"/>
    </svg>

    <header class="holder">
      <h1 class="holder-name">CALDER VOSS</h1>
      <p class="holder-title">PRESIDENT</p>
    </header>

    <address class="address">
      2917 Harrow Lane<br>
      Alder Point, NY 10472
    </address>

    <ul class="contact-list">
      <li>
        <svg class="contact-icon" viewBox="0 0 24 24" aria-hidden="true"><path d="M6.6 10.8a15.1 15.1 0 0 0 6.6 6.6l2.2-2.2a1 1 0 0 1 1-.25 11.4 11.4 0 0 0 3.6.57 1 1 0 0 1 1 1V20a1 1 0 0 1-1 1A17 17 0 0 1 3 4a1 1 0 0 1 1-1h3.5a1 1 0 0 1 1 1c0 1.250.2 2.450.57 3.57a1 1 0 0 1-.25 1z"/></svg>
        555 0142 7316
      </li>
      <li>
        <svg class="contact-icon" viewBox="0 0 24 24" aria-hidden="true"><path d="M7 3h10v5H7zM4 9h16a2 2 0 0 1 2 2v6h-4v4H6v-4H2v-6a2 2 0 0 1 2-2zm4 6v4h8v-4z"/></svg>
        555 0198 2047
      </li>
      <li>
        <svg class="contact-icon" viewBox="0 0 24 24" aria-hidden="true"><path d="M3 5h18v14H3zm2 2v.5l7 4.5 7-4.5V7z"/></svg>
        calder@brellwick.com
      </li>
      <li class="web">
        <svg class="contact-icon" viewBox="0 0 24 24" aria-hidden="true"><circle cx="12" cy="12" r="9" fill="none" stroke="#c9d2e2" stroke-width="2"/><path d="M3 12h18M12 3c3 3 3 15 0 18M12 3c-3 3-3 15 0 18" fill="none" stroke="#c9d2e2" stroke-width="1.6"/></svg>
        www.brellwick.com
      </li>
    </ul>

    <div class="brand">
      <span class="brand-mark" aria-hidden="true"></span>
      <div class="brand-text">
        <p class="brand-name">BRELLWICK</p>
        <p class="brand-suffix">PARTNERS, LLC</p>
        <p class="brand-tagline">Financial Planning and Consulting</p>
      </div>
    </div>
  </section>
</body>
</html>
```